African homeware retailer needs a web page design

We need a web page design for a new homeware and accessories store based in Johannesburg, South Africa. Our store carries modern African inspired items from designers that support social development and poverty alleviation initiatives. We have a particular preference for outfits that are centred on the empowerment of women.

Our business celebrates the skill, design and product of African craft and the work of designers looking to take that forward in a socially beneficial way (creating employment, developing skills, supporting local crafts people etc). We aim to carry items and inspirations from all over the African continent.

We would like to see a design that communicates African beauty and elegance without the typical tribal references that are made in reference to African craft or art.

We would like the web page to be stylish, uncomplicated, modern, captivating and appealing to the discerning customer. A similar value proposition is that of http://www.marlowtenwick.example/.

This is an e-commerce website which must be attractive to both individual buyers and design professionals so the website needs to look professional.

Here are links to some websites we like:
http://www.quenbyhollis.example/
http://www.dravelo.example/

Our logo is attached to the brief.

Target Market(s)

Our target market is female, age 20-50. However should not alienate the design conscious male customer therefore

Industry/Entity Type

E-Commerce

Requirements
Must have
• - A featured product banner which includes a photograph and text. This should be easy to edit as we will be changing the featured product regularly
- An easily expendable products section with categories. Examples of categories could be cushions, bedding, crockery etc. Should be easy to add new categories as well as new product pictures
- Home/landing page should be uncluttered
- Should use the logo and should be easy to change the logo which we have in various colour combinations. We plan to change the logo colours depending on circumstance e.g. make it red and white around Valentines day (similar to the way Vintrel frequently changes the logo on their landing page)

```html
<!DOCTYPE html>
<html lang="en">
<head>
<meta charset="utf-8">
<title>Kaya Atelier — Homeware &amp; Accessories</title>
<link href="https://fonts.googleapis.com/css2?family=Noto+Sans:wght@400;700&display=swap" rel="stylesheet">
<style>
:root{
  --teal:#1a9fa0;
  --orange:#d9480f;
  --yellow:#f7f48f;
  --page:#fafafa;
  --panel:#eeeeee;
  --panel-light:#f3f3f3;
  --ink:#555555;
  --ink-dark:#444444;
  --white:#ffffff;
}
*{box-sizing:border-box;margin:0;padding:0}
html,body{width:772px;height:1200px;overflow:hidden}
body{position:relative;background:var(--page);font-family:"Noto Sans",Verdana,sans-serif;color:var(--ink)}
.abs{position:absolute}

/* header */
.account-bar{left:442px;top:0;width:248px;height:21px;background:var(--teal);border-radius:11px;color:var(--white);font-size:9px;font-weight:700;display:flex;align-items:center;justify-content:center;gap:6px}
.search{left:566px;top:34px;width:124px;height:15px;border:1px solid #bbb;background:var(--white);font-size:8px;color:#999;padding:1px 8px;display:flex;justify-content:space-between;align-items:center}
.brand{left:84px;top:74px;display:flex;align-items:center;gap:6px}
.brand-mark{width:12px;height:12px;background:var(--orange)}
.brand-name{font-size:14px;font-weight:700;color:var(--orange);letter-spacing:.6px}
.call{right:82px;top:67px;display:flex;gap:5px;align-items:center}
.call .label{font-size:11px;color:var(--teal);line-height:1.1}
.call .number{font-size:11.5px;font-weight:700;color:var(--orange);line-height:1.2}
.nav{left:81px;top:117px;display:flex;gap:5px;font-size:9.6px;color:var(--ink)}
.nav .current{color:var(--orange);font-weight:700}
.nav .sep{font-size:8px;margin-top:1px}
.rule{left:4px;top:140px;width:766px;border-top:1px dashed #777}

/* hero */
.hero{left:78px;top:157px;width:613px;height:233px;background:#fbf4ec}
.hero-photo{left:0;top:0;width:318px;height:233px;border-right:1px solid #f1e6d8;
  background:linear-gradient(135deg,#f6e8d4 0%,#e4c18b 28%,#d6a865 48%,#c8945a 58%,#2e3c86 68%,#3a4c9a 74%,#e2bf88 84%,#f6e8d4 100%)}
.hero-card{left:350px;top:33px;width:170px;height:156px;background:#fdfaf6;text-align:center;padding-top:30px}
.hero-card p{font-size:10.4px;font-weight:700;color:var(--ink-dark);line-height:14px}
.order{display:inline-block;margin-top:24px;background:var(--orange);color:var(--white);font-size:10.4px;font-weight:700;padding:2px 13px;letter-spacing:.5px}
.dots{left:415px;top:204px;display:flex;gap:3px}
.dots span{width:7px;height:7px;border-radius:50%;border:1px solid #999}
.dots .on{border:2px solid var(--orange)}

/* promo tiles */
.tile{top:405px;width:291px;height:115px;background:var(--yellow);border:8px solid var(--orange)}
.tile-story{left:80px}
.tile-design{left:400px}
.tile h2{position:absolute;color:var(--teal);font-weight:700;font-size:24px;line-height:27px}
.tile-story h2{left:22px;top:34px}
.tile-design h2{left:20px;top:8px}
.tile-photo{position:absolute;right:0;top:0;width:88px;height:99px;background:linear-gradient(170deg,#3f3f4a 0%,#6e6c78 35%,#b98a70 60%,#e8e3dc 100%)}
.tile-plate{position:absolute;right:0;top:0;width:120px;height:99px;background:radial-gradient(ellipse at 50% 50%,#d09a6d 0,#b07246 45%,#6b4228 75%,#f2ee96 100%)}

/* shop */
.shop{left:78px;top:547px;width:613px;height:360px;background:var(--panel)}
.cat-col{left:0;top:0;width:130px;height:360px;background:var(--panel-light);border-right:1px dashed #ddd}
.col-head{height:28px;display:flex;align-items:center;justify-content:center;font-size:9.6px;font-weight:700;color:var(--orange)}
.feat-head{left:131px;top:0;width:482px;height:28px;background:var(--page)}
.cat{position:absolute;left:0;width:129px;height:24px;display:flex;align-items:center;justify-content:space-between;padding:0 11px 0 38px;color:var(--white);font-size:10.4px;font-weight:700}
.cat i{font-style:normal;width:9px;height:9px;font-size:9px;line-height:8px;text-align:center}
.cat-open{top:28px;background:var(--teal)}
.cat-open i{background:var(--orange)}
.cat-closed{background:var(--orange)}
.cat-closed i{background:var(--teal)}
.sub{position:absolute;left:40px;top:58px;list-style:none;font-size:8.8px;line-height:14.6px;color:var(--ink)}
.product{position:absolute;width:120px;text-align:center}
.diamond{width:84px;height:84px;margin:0 auto;transform:rotate(45deg);border:4px solid var(--orange);border-radius:3px}
.product .name{margin-top:27px;font-size:9.6px;font-weight:700;color:var(--ink)}
.next{left:592px;top:161px;width:21px;height:60px;background:var(--page);border-radius:8px 0 0 8px}

/* footer */
.footer{left:78px;top:934px;width:613px;height:188px;border-top:1px solid #aaa;background:var(--panel)}
.f-title{position:absolute;font-size:13.6px;font-weight:400;color:var(--teal)}
.links{position:absolute;left:40px;top:45px;list-style:none;font-size:9.6px;line-height:16px;color:var(--ink)}
.vdash{position:absolute;top:16px;height:156px;border-left:1px dashed #999}
.field{position:absolute;left:187px;width:183px;height:18px;background:var(--white);border:1px solid #ccc;border-radius:2px;font-size:7.5px;font-style:italic;color:#777;padding:3px 6px}
.submit{position:absolute;left:188px;top:164px;width:43px;height:15px;background:var(--orange);color:var(--white);font-size:9px;font-weight:700;text-align:center;line-height:15px}
.news{position:absolute;left:416px;top:42px;width:160px;height:27px;background:#bdbdbd;padding:5px 6px;display:flex;gap:3px}
.news .email{flex:1;background:var(--white);font-size:8px;color:#777;padding:1px 5px}
.news .go{width:28px;background:var(--white)}
.news-note{position:absolute;left:423px;top:81px;font-size:9.6px;color:var(--ink)}
.social{position:absolute;left:415px;top:149px;display:flex;gap:5.6px}
.social span{width:20px;height:20px;border-radius:50%;background:var(--teal)}
.pay{left:78px;top:1122px;width:613px;height:53px;background:#dedede;text-align:center}
.pay h3{font-weight:400;font-size:10.8px;color:var(--teal);margin-top:9px}
.cards{display:flex;justify-content:center;gap:4px;margin-top:5px}
.cards span{width:27px;height:17px;border-radius:2px;background:#8a8fa8}
.copy{left:0;top:1182px;width:772px;text-align:center;font-size:8px;color:var(--ink)}
</style>
</head>
<body>

<header>
  <div class="abs account-bar"><span>Login</span>|<span>Sign Up</span>|<span>My Account</span>|<span>Shopping Cart</span></div>
  <div class="abs search"><span>Search</span>
    <svg width="9" height="9" viewBox="0 0 10 10"><circle cx="4" cy="4" r="3" fill="none" stroke="#888" stroke-width="1.4"/><line x1="6.2" y1="6.2" x2="9.3" y2="9.3" stroke="#888" stroke-width="1.6"/></svg>
  </div>
  <div class="abs brand"><span class="brand-mark"></span><span class="brand-name">Kaya Atelier</span></div>
  <div class="abs call">
    <svg width="10" height="20" viewBox="0 0 10 20"><path d="M7 1 Q1 3 1 10 Q1 17 7 19 L8.5 15.5 Q5 14 5 10 Q5 6 8.5 4.5 Z" fill="#222"/></svg>
    <div><div class="label">Call us</div><div class="number">123-456-7890</div></div>
  </div>
  <nav class="abs nav">
    <span class="current">Shop Now</span><span class="sep">&gt;</span>
    <span>Our Story</span><span class="sep">&gt;</span>
    <span>Blog</span><span class="sep">&gt;</span>
    <span>Custom Design</span><span class="sep">&gt;</span>
    <span>Our Shop</span><span class="sep">&gt;</span>
    <span>Press &amp; Mentions</span><span class="sep">&gt;</span>
    <span>Designer &amp; Architects</span><span class="sep">&gt;</span>
    <span>Video</span><span class="sep">&gt;</span>
    <span>Contact</span>
  </nav>
  <div class="abs rule"></div>
</header>

<section class="abs hero">
  <div class="abs hero-photo" role="img" aria-label="Featured product photo: wooden serving boards with blue printed napkins"></div>
  <div class="abs hero-card">
    <p>Lorem ipsum lorelorem<br>loremipsuim lorem<br>lorem ipsum loremlorem<br>loremipsuim lorem<br>lorem ipsum loremlorem</p>
    <span class="order">ORDER NOW</span>
  </div>
  <div class="abs dots"><span></span><span></span><span class="on"></span><span></span></div>
</section>

<a class="abs tile tile-story">
  <h2>Our Story</h2>
  <div class="tile-photo" role="img" aria-label="Portrait photo of a crafter wearing a beaded headdress"></div>
</a>
<a class="abs tile tile-design">
  <h2>Designer<br>&amp;<br>Architects</h2>
  <div class="tile-plate" role="img" aria-label="Photo of a hand-painted ceramic bowl"></div>
</a>

<section class="abs shop">
  <aside class="abs cat-col">
    <div class="col-head">CATEGORIES</div>
    <div class="cat cat-open">Cushions<i>-</i></div>
    <ul class="sub"><li>Lorem ipsum</li><li>Lorem ipsum</li><li>Lorem ipsum</li><li>Lorem ipsum</li></ul>
    <div class="cat cat-closed" style="top:126px">Bedding<i>+</i></div>
    <div class="cat cat-closed" style="top:162px">Crockery<i>+</i></div>
  </aside>
  <div class="abs feat-head col-head">FEATURED PRODUCTS</div>

  <div class="product" style="left:175px;top:58px"><div class="diamond" role="img" aria-label="Product photo: beaded wire bicycle sculpture" style="background:linear-gradient(135deg,#1e1e1e 0%,#4a4a4a 35%,#cfcfcf 55%,#c5512a 75%,#2a2a2a 100%)"></div><div class="name">LOREM IPSUM</div></div>
  <div class="product" style="left:312px;top:58px"><div class="diamond" role="img" aria-label="Product photo: red and cream woven plates" style="background:linear-gradient(135deg,#1a1a1a 0%,#b1141b 25%,#a0101a 48%,#efe8cf 52%,#e8dfc0 85%,#222 100%)"></div><div class="name">LOREM IPSUM</div></div>
  <div class="product" style="left:449px;top:58px"><div class="diamond" role="img" aria-label="Product photo: beaded wire creatures" style="background:linear-gradient(135deg,#e4e4e4 0%,#9bb060 35%,#dcdcdc 50%,#c42a3a 70%,#d9d9d9 100%)"></div><div class="name">LOREM IPSUM</div></div>

  <div class="product" style="left:175px;top:224px"><div class="diamond" role="img" aria-label="Product photo: white ceramic vessels" style="background:linear-gradient(135deg,#4a4a4a 0%,#8c8a86 25%,#f2eee6 50%,#d9d3c7 75%,#f4f1ea 100%)"></div><div class="name">LOREM IPSUM</div></div>
  <div class="product" style="left:312px;top:224px"><div class="diamond" role="img" aria-label="Product photo: woven baskets" style="background:linear-gradient(135deg,#3c3c3c 0%,#d7b47a 30%,#6b4526 50%,#e0c28c 70%,#3a2616 100%)"></div><div class="name">LOREM IPSUM</div></div>
  <div class="product" style="left:449px;top:224px"><div class="diamond" role="img" aria-label="Product photo: striped woven wire bowl" style="background:linear-gradient(135deg,#eeeeee 0%,#e6d21f 30%,#4a4a4a 45%,#f4f4f4 58%,#e6d21f 70%,#555 85%,#eee 100%)"></div><div class="name">LOREM IPSUM</div></div>

  <div class="abs next"><svg width="21" height="60" viewBox="0 0 21 60"><polyline points="8,22 14,30 8,38" fill="none" stroke="#aaa" stroke-width="1.5"/></svg></div>
</section>

<footer>
  <div class="abs footer">
    <h3 class="f-title" style="left:38px;top:10px">Quick Links</h3>
    <ul class="links"><li>Shop Now</li><li>Our Story</li><li>Blog</li><li>Custom Design</li><li>Our Shop</li><li>Press &amp; Mentions</li><li>Designer &amp; Architects</li><li>Video</li><li>Contact</li></ul>
    <div class="vdash" style="left:165px"></div>

    <h3 class="f-title" style="left:188px;top:10px">QUICK CONTACT</h3>
    <div class="field" style="top:41px">Name</div>
    <div class="field" style="top:63px">Phone</div>
    <div class="field" style="top:85px">Email</div>
    <div class="field" style="top:107px;height:47px">Message</div>
    <div class="submit">Submit</div>
    <div class="vdash" style="left:391px"></div>

    <h3 class="f-title" style="left:414px;top:10px">NEWSLETTER</h3>
    <div class="news"><span class="email">your email...</span><span class="go"></span></div>
    <p class="news-note">Leave your email to subscribe</p>
    <h3 class="f-title" style="left:414px;top:114px">FOLLOW US ON</h3>
    <div class="social"><span></span><span></span><span></span><span></span><span></span><span></span></div>
  </div>
  <div class="abs pay">
    <h3>SECURE PAYMENT</h3>
    <div class="cards"><span></span><span></span><span></span><span></span><span></span><span></span></div>
  </div>
  <p class="abs copy">© 2014. KayaAtelier. All Rights Reserved.</p>
</footer>

</body>
</html>
```